Business Card Design Project

This is the first time we use our new logo. We need a business card that we can use both on our institutional corporate relationships and also that works for our staff that deals with consumers directly.

VELUNDA is a new company dedicated to empower consumers and to provide them with the best choices for specialized health care using the latest telemedicine technology (medicine at a distance via videoconference).

We want to print this cards in high quality materials and process. We will like designs that allow us to use UV spot varnish and other techniques that will differentiate us.

We are including Two different versions of Color logos. In addition we are including white over black background logos. Those can be used replacing the black for a color.

Please note this is the first time we will be creating any corporate materials with our new logo and colors.

Target Market(s)

34+ consumers of medium high and high socioeconomic levels.

Industry/Entity Type

Health

Requirements
Must have
• Our logo on its original colors
Should not have
• Any other graphical element or design that is not our logo

```html
<!DOCTYPE html>
<html lang="en">
<head>
<meta charset="utf-8">
<title>VELUNDA business card</title>
<link rel="stylesheet" href="https://fonts.googleapis.com/css2?family=Montserrat:wght@400;700&family=Arimo:wght@400&display=swap">
<style>
  :root {
    --navy: #1b5a88;
    --blue: #1f72b8;
    --sky: #5ab5de;
    --teal: #17a597;
    --ink: #1c1c1c;
    --rule: #cfcfcf;
    --paper: #ffffff;
    --backdrop: #e9eaee;
  }
  html, body {
    margin: 0;
    width: 1200px;
    height: 987px;
    overflow: hidden;
    background: var(--backdrop);
  }
  .sheet {
    position: relative;
    width: 1200px;
    height: 987px;
    display: flex;
    flex-direction: column;
    align-items: center;
    justify-content: center;
    gap: 60px;
  }
  .card {
    position: relative;
    width: 700px;
    height: 400px;
    background: var(--paper);
    border-radius: 30px;
    overflow: hidden;
    box-shadow: 0 4px 14px rgba(0,0,0,0.12);
  }
  .wordmark {
    display: flex;
    align-items: center;
    gap: 14px;
  }
  .wordmark-dot {
    width: 26px;
    height: 26px;
    border-radius: 50%;
    background: var(--teal);
  }
  .wordmark-name {
    font-family: "Montserrat", sans-serif;
    font-weight: 700;
    color: var(--navy);
    letter-spacing: 3px;
  }

  /* Back */
  .card-back {
    display: flex;
    flex-direction: column;
    align-items: center;
    justify-content: center;
    gap: 26px;
  }
  .card-back .wordmark-name { font-size: 56px; }
  .card-back .site {
    font-family: "Arimo", sans-serif;
    font-size: 20px;
    letter-spacing: 5px;
    color: #333;
  }
  .card-back .site b { color: var(--navy); font-weight: 400; }

  /* Front */
  .waves {
    position: absolute;
    inset: 0;
  }
  .card-front .wordmark {
    position: absolute;
    left: 36px;
    top: 138px;
  }
  .card-front .wordmark-name { font-size: 46px; }
  .divider {
    position: absolute;
    left: 372px;
    top: 50px;
    width: 1px;
    height: 230px;
    background: var(--rule);
  }
  .contact {
    position: absolute;
    left: 400px;
    top: 48px;
    font-family: "Arimo", sans-serif;
    color: var(--ink);
  }
  .contact-name {
    font-family: "Montserrat", sans-serif;
    font-weight: 700;
    font-size: 28px;
    color: var(--navy);
    margin: 0;
    line-height: 1.1;
  }
  .contact-title {
    font-size: 20px;
    color: var(--teal);
    margin: 0 0 14px;
  }
  .contact-list {
    list-style: none;
    margin: 0;
    padding: 0;
    font-size: 19px;
    line-height: 29px;
  }
  .contact-list li {
    display: flex;
    align-items: center;
    gap: 8px;
  }
  .contact-list svg { width: 16px; height: 16px; flex: none; }
  .address {
    margin: 8px 0 0;
    font-size: 19px;
    line-height: 23px;
  }
</style>
</head>
<body>
<main class="sheet">

  <section class="card card-back" aria-label="Card back">
    <div class="wordmark">
      <span class="wordmark-dot"></span>
      <span class="wordmark-name">VELUNDA</span>
    </div>
    <div class="site">www.<b>velunda</b>.com</div>
  </section>

  <section class="card card-front" aria-label="Card front">
    <svg class="waves" viewBox="0 0 700 400" preserveAspectRatio="none" aria-hidden="true">
      <path class="wave-stripe" d="M0 220 C220 215 420 300 700 318 L700 400 L0 400Z" fill="var(--blue)"/>
      <path class="wave-gap" d="M0 236 C220 232 420 318 700 326 L700 400 L0 400Z" fill="var(--paper)"/>
      <path class="wave-light" d="M0 250 C220 248 420 330 700 332 L700 400 L0 400Z" fill="var(--sky)"/>
      <path class="wave-base" d="M0 252 C220 252 420 352 700 362 L700 400 L0 400Z" fill="var(--navy)"/>
    </svg>

    <div class="wordmark">
      <span class="wordmark-dot"></span>
      <span class="wordmark-name">VELUNDA</span>
    </div>

    <div class="divider"></div>

    <div class="contact">
      <p class="contact-name">Your Name</p>
      <p class="contact-title">Title</p>
      <ul class="contact-list">
        <li>
          <svg viewBox="0 0 16 16"><circle cx="8" cy="8" r="7" fill="none" stroke="var(--navy)" stroke-width="1.5"/><path d="M5.5 4.5 L7 6 L6.2 7.2 C6.8 8.4 7.6 9.2 8.8 9.8 L10 9 L11.5 10.5 L10.5 11.5 C7.5 11 5 8.5 4.5 5.5Z" fill="var(--navy)"/></svg>
          012-345-6789
        </li>
        <li>
          <svg viewBox="0 0 16 16"><circle cx="8" cy="8" r="7" fill="none" stroke="var(--navy)" stroke-width="1.5"/><path d="M5.5 4.5 L7 6 L6.2 7.2 C6.8 8.4 7.6 9.2 8.8 9.8 L10 9 L11.5 10.5 L10.5 11.5 C7.5 11 5 8.5 4.5 5.5Z" fill="var(--navy)"/></svg>
          012-345-6789
        </li>
        <li>
          <svg viewBox="0 0 16 16"><rect x="1" y="3.5" width="14" height="9" rx="1" fill="var(--navy)"/><path d="M1.5 4 L8 9 L14.5 4" fill="none" stroke="#fff" stroke-width="1.2"/></svg>
          name@velunda.com
        </li>
        <li>
          <svg viewBox="0 0 16 16"><circle cx="8" cy="8" r="7" fill="none" stroke="var(--navy)" stroke-width="1.4"/><ellipse cx="8" cy="8" rx="3" ry="7" fill="none" stroke="var(--navy)" stroke-width="1.1"/><path d="M1 8 H15 M2.5 4.5 H13.5 M2.5 11.5 H13.5" stroke="var(--navy)" stroke-width="1.1"/></svg>
          www.velunda.com
        </li>
      </ul>
      <p class="address">Street Name, City Name<br>State, City Zip Code</p>
    </div>
  </section>

</main>
</body>
</html>
```